Dietitian needs awesome business card

I need a contemporary design that's eye catching but professional.
My card is to given to doctors, specialists and patients alike.
I manage patients with chronic diseases
I have uploaded my logo and current business card, I would also like the other Certified Clinical Nutritionist logo incorporated into the design

Target Market(s)

Doctors, specialists and patients

Industry/Entity Type

Healthcare

Contact Information for Business Card

www.brightfieldnutrition.com.au
Ph: 0427 561 903
Fax: 6457 2183
email: marcus.k.diet@fernmail.com
Space on the back of the card with: Appointment date, Appointment time and appointment location

Font styles to use
Serif

Colors
fbee3e
876aae
ffc214

Requirements
Must have
• My Logo
• Certified Clinical Nutritionist Logo
• My 4 locations - Pinebrook Medical Centre, North Corrin Health, Hollis Medical, Ashcombe Doctors Surgery
Nice to have
• I like the colours in my current business card

```html
<!DOCTYPE html>
<html lang="en">
<head>
<meta charset="utf-8">
<title>Brightfield Nutrition &amp; Dietetics – Business Card</title>
<link href="https://fonts.googleapis.com/css2?family=Open+Sans:ital,wght@0,400;0,600;1,400&display=swap" rel="stylesheet">
<style>
  :root {
    --backdrop: #2a2a2a;
    --card: #ffffff;
    --navy: #1f3a93;
    --green: #7ab829;
    --badge: #f47920;
    --ink: #3c3c3c;
    --rule: #9aa0b8;
    --divider: #cfcfcf;
    --muted: #555555;
  }
  * { margin: 0; padding: 0; box-sizing: border-box; }
  html, body { width: 1200px; height: 987px; overflow: hidden; }
  body {
    background: var(--backdrop);
    font-family: "Open Sans", Arial, sans-serif;
    position: relative;
  }
  .card {
    position: absolute;
    width: 615px;
    height: 352px;
    background: var(--card);
    box-shadow: 0 4px 14px rgba(0,0,0,0.5);
  }
  .card--front { left: 293px; top: 130px; }
  .card--back  { left: 292px; top: 505px; }

  /* brand block */
  .brand { position: absolute; display: flex; align-items: center; gap: 10px; }
  .brand__dot { width: 44px; height: 44px; border-radius: 50%; background: var(--green); flex: none; }
  .brand__name { color: var(--navy); font-weight: 400; line-height: 1.05; }
  .brand__name span { display: block; }
  .card--front .brand { left: 40px; top: 152px; }
  .card--front .brand__name span:first-child { font-size: 31px; }
  .card--front .brand__name span:last-child { font-size: 13.5px; }
  .card--back .brand { left: 50%; top: 58px; transform: translateX(-50%); gap: 14px; }
  .card--back .brand__dot { width: 62px; height: 62px; }
  .card--back .brand__name span:first-child { font-size: 42px; }
  .card--back .brand__name span:last-child { font-size: 18.5px; }

  .divider { position: absolute; left: 294px; top: 89px; width: 1px; height: 180px; background: var(--divider); }

  .person { position: absolute; left: 316px; top: 86px; }
  .person__name { color: var(--navy); font-size: 22px; font-weight: 600; line-height: 1.2; }
  .person__role { color: var(--green); font-size: 16px; line-height: 1.3; }

  .badge { position: absolute; left: 316px; top: 146px; width: 74px; height: 34px; background: var(--badge); }

  .contacts { position: absolute; left: 316px; top: 193px; list-style: none; }
  .contacts li { display: flex; align-items: center; gap: 8px; color: var(--ink); font-size: 16px; height: 24px; }
  .contacts svg { width: 16px; height: 16px; fill: var(--navy); flex: none; }

  .appointment { position: absolute; left: 40px; right: 42px; color: var(--navy); font-size: 16px; display: flex; align-items: flex-end; }
  .appointment--when { top: 208px; }
  .appointment--where { top: 259px; }
  .field-line { border-bottom: 1px solid var(--rule); height: 14px; margin: 0 8px 3px 8px; }
  .field-line--date { width: 250px; }
  .field-line--time { width: 118px; margin-right: 6px; }
  .field-line--location { flex: 1; margin-right: 0; }
  .ampm { font-size: 13px; }

  .website {
    position: absolute; left: 0; right: 0; top: 302px;
    text-align: center; font-style: italic; font-size: 15px;
    letter-spacing: 2.6px; color: var(--muted);
  }
</style>
</head>
<body>

<section class="card card--front" aria-label="Card front">
  <div class="brand">
    <div class="brand__dot"></div>
    <div class="brand__name"><span>Brightfield</span><span>Nutrition &amp; Dietetics</span></div>
  </div>
  <div class="divider"></div>
  <div class="person">
    <p class="person__name">Marcus Kellaway</p>
    <p class="person__role">Nutritionist &amp; Chef</p>
  </div>
  <div class="badge" role="img" aria-label="Certified Clinical Nutritionist badge"></div>
  <ul class="contacts">
    <li>
      <svg viewBox="0 0 16 16" aria-hidden="true"><path d="M3.6 1.5 6 4.2 4.7 6a9 9 0 0 0 5.3 5.3l1.8-1.3 2.7 2.4-1.3 2C8 14.6 1.4 8 1.6 2.8z"/></svg>
      0427 561 903
    </li>
    <li>
      <svg viewBox="0 0 16 16" aria-hidden="true"><rect x="4" y="1.5" width="8" height="4"/><rect x="1" y="6.5" width="14" height="6" rx="1"/><rect x="3" y="11" width="10" height="3.5" fill="#fff" stroke="#1f3a93" stroke-width="1"/></svg>
      6457 2183
    </li>
    <li>
      <svg viewBox="0 0 16 16" aria-hidden="true"><rect x="1" y="3.5" width="14" height="10"/><path d="M1.5 4 8 9.2 14.5 4" fill="none" stroke="#fff" stroke-width="1.2"/></svg>
      marcus.k.diet@fernmail.com
    </li>
  </ul>
</section>

<section class="card card--back" aria-label="Card back">
  <div class="brand">
    <div class="brand__dot"></div>
    <div class="brand__name"><span>Brightfield</span><span>Nutrition &amp; Dietetics</span></div>
  </div>
  <div class="appointment appointment--when">
    <span>Date :</span><span class="field-line field-line--date"></span>
    <span>Time :</span><span class="field-line field-line--time"></span>
    <span class="ampm">AM/PM</span>
  </div>
  <div class="appointment appointment--where">
    <span>Location :</span><span class="field-line field-line--location"></span>
  </div>
  <p class="website">www.brightfieldnutrition.com.au</p>
</section>

</body>
</html>
```